Furniture Removalist needs Chatterlane design

I already have a Chatterlane page for my business.

I would like the style to match my logo and business card..

Let me know what other information you will need, as I'm not sure?

```html
<!DOCTYPE html>
<html lang="en">
<head>
<meta charset="utf-8">
<title>Harlow Removals – Chatterlane Cover and Profile Image</title>
<link rel="stylesheet" href="https://fonts.googleapis.com/css2?family=Open+Sans:wght@300;400;600&display=swap">
<style>
  :root {
    --brand-orange: #f26a21;
    --brand-grey: #6d6e70;
    --brand-grey-dark: #58595b;
    --paper: #ffffff;
    --stage: #ece8e3;
    --label-ink: #2b2b2b;
    --photo-light: #fbf3e2;
    --photo-mid: #e9cfa4;
    --photo-deep: #c99a62;
  }
  * { box-sizing: border-box; margin: 0; padding: 0; }
  html, body { width: 1029px; height: 1200px; overflow: hidden; }
  body {
    background: var(--stage);
    font-family: "Open Sans", Arial, sans-serif;
    position: relative;
  }

  /* ---------- Cover ---------- */
  .cover {
    position: absolute;
    left: 35px; top: 150px;
    width: 960px; height: 354px;
    overflow: hidden;
    background: var(--paper);
    box-shadow: 0 2px 6px rgba(0,0,0,.25);
  }
  .cover__photo {
    position: absolute;
    left: 380px; top: 0;
    width: 580px; height: 354px;
    background:
      linear-gradient(90deg, rgba(242,106,33,0) 0%, rgba(242,106,33,0) 100%),
      linear-gradient(160deg, var(--photo-light) 0%, var(--photo-mid) 55%, var(--photo-deep) 100%);
  }
  .cover__logo-strip {
    position: absolute;
    left: 0; top: 0;
    width: 420px; height: 70px;
    background: var(--paper);
    display: flex; align-items: center; gap: 12px;
    padding-left: 14px;
  }
  .brand-mark {
    width: 46px; height: 46px;
    border: 2px solid var(--brand-grey);
  }
  .brand-name {
    font-weight: 300;
    font-size: 34px;
    color: var(--brand-grey);
    letter-spacing: .3px;
    line-height: 1;
  }
  .cover__services {
    position: absolute;
    left: 0; top: 70px;
    width: 420px; height: 181px;
    background: var(--brand-orange);
    list-style: none;
    padding: 12px 0 0 36px;
  }
  .cover__services li {
    display: flex; align-items: center; gap: 6px;
    color: var(--paper);
    font-size: 16.5px;
    line-height: 22.7px;
  }
  .cover__services svg { width: 15px; height: 15px; flex: none; fill: var(--paper); }
  .cover__base {
    position: absolute;
    left: 0; top: 251px;
    width: 420px; height: 103px;
    background: var(--brand-grey);
  }

  /* ---------- Profile image ---------- */
  .profile {
    position: absolute;
    left: 35px; top: 630px;
    width: 300px; height: 300px;
    overflow: hidden;
    box-shadow: 0 2px 6px rgba(0,0,0,.25);
    background: var(--brand-orange);
  }
  .profile__band {
    position: absolute;
    left: 0; top: 90px;
    width: 300px; height: 160px;
    background: var(--brand-grey);
  }
  .profile__box {
    position: absolute;
    left: 62px; top: 28px;
    width: 176px; height: 248px;
    background: var(--paper);
  }

  /* ---------- Labels ---------- */
  .caption {
    position: absolute;
    font-size: 22px;
    font-weight: 400;
    color: var(--label-ink);
    letter-spacing: .5px;
  }
  .caption--cover { left: 35px; width: 960px; top: 518px; text-align: center; }
  .caption--profile { left: 35px; width: 300px; top: 944px; text-align: center; }
</style>
</head>
<body>

  <section class="cover" aria-label="Chatterlane cover">
    <div class="cover__photo" role="img" aria-label="Photo of a couple packing cardboard moving boxes in a bright room"></div>
    <div class="cover__logo-strip">
      <span class="brand-mark"></span>
      <span class="brand-name">Harlow Removals</span>
    </div>
    <ul class="cover__services">
      <li><svg viewBox="0 0 16 16"><rect x="1" y="4" width="9" height="7"/><rect x="10" y="6" width="5" height="5"/><circle cx="4" cy="13" r="2"/><circle cx="12" cy="13" r="2"/></svg>Local, Country &amp; Interstate Removals</li>
      <li><svg viewBox="0 0 16 16"><path d="M8 1 L15 8 H13 V15 H10 V10 H6 V15 H3 V8 H1 Z"/></svg>Home &amp; Hi Rise Removals</li>
      <li><svg viewBox="0 0 16 16"><path d="M2 3 L8 9 L14 3 L15 5 L9 11 V15 H7 V11 L1 5 Z"/></svg>Office &amp; Factory Relocation's</li>
      <li><svg viewBox="0 0 16 16"><rect x="3" y="2" width="10" height="12" rx="2"/></svg>Pre - Packing &amp; Unpacking Service's</li>
      <li><svg viewBox="0 0 16 16"><rect x="2" y="7" width="12" height="8"/><path d="M1 7 L8 2 L15 7 Z"/></svg>Storage Solution</li>
    </ul>
    <div class="cover__base"></div>
  </section>
  <p class="caption caption--cover">Chatterlane Cover</p>

  <section class="profile" aria-label="Profile image">
    <div class="profile__band"></div>
    <div class="profile__box" role="img" aria-label="White line illustration of an open moving box"></div>
  </section>
  <p class="caption caption--profile">Profile Image</p>

</body>
</html>
```